Simple and Clean business card design

We would like the design to be simple clean and to incorporate our colors.

We are open to your design and talent, we have the dots in our logo as we think of it as data points and we connect data points for people.

We are open to see the great creative and clean design you bring to the table

Contact Information for Business Card

please include: name, position, email, phone and website

Font styles to use
Sans Serif

Requirements
Must have
• my colors incorporated, simplicity
Nice to have
• lots of white space, simplicity
Should not have
• complexicity/ complex art

```html
<!DOCTYPE html>
<html lang="en">
<head>
<meta charset="utf-8">
<title>Nectara business card</title>
<link rel="stylesheet" href="https://fonts.googleapis.com/css2?family=Arimo:wght@400;700&display=swap">
<style>
  :root {
    --stage: #2a2a2a;
    --blue: #4a86e8;
    --green: #2ea652;
    --yellow: #f2c200;
    --orange: #f59a1e;
    --red: #e2483a;
    --ink: #111111;
    --paper: #ffffff;
    --paper-shade: #ececec;
  }
  * { box-sizing: border-box; margin: 0; padding: 0; }
  html, body {
    width: 1200px; height: 901px; overflow: hidden;
    background: var(--stage);
    font-family: "Arimo", Arial, sans-serif;
  }
  .stage {
    position: relative; width: 1200px; height: 901px;
  }
  .card {
    position: absolute; left: 250px; width: 700px; height: 400px;
    overflow: hidden;
  }
  .card--front {
    top: 30px;
    background: linear-gradient(180deg,
      #5b9af0 0%, #3fa8a8 28%, var(--green) 44%,
      #b9cf2a 56%, var(--yellow) 66%, var(--orange) 82%, var(--red) 100%);
  }
  .card--back {
    top: 471px;
    background: radial-gradient(ellipse at 55% 40%, var(--paper) 45%, var(--paper-shade) 100%);
  }
  .brand {
    position: absolute; display: flex; align-items: center; gap: 14px;
    font-weight: 700; letter-spacing: 1px; line-height: 1;
  }
  .brand__dot { border-radius: 50%; flex: none; }
  .card--front .brand {
    left: 0; right: 0; top: 150px; justify-content: center;
    color: var(--paper); font-size: 92px;
  }
  .card--front .brand__dot { width: 26px; height: 26px; background: var(--paper); }
  .card--back .brand {
    right: 60px; top: 70px; color: var(--ink); font-size: 74px;
  }
  .card--back .brand__dot { width: 22px; height: 22px; background: var(--blue); }

  .person { position: absolute; left: 70px; top: 178px; }
  .person__name { color: var(--blue); font-weight: 700; font-size: 30px; letter-spacing: .5px; }
  .person__role { color: var(--ink); font-size: 20px; margin-top: 4px; }

  .divider {
    position: absolute; left: 60px; right: 70px; top: 244px;
    height: 2px; background: var(--ink);
  }

  .contacts { position: absolute; left: 62px; top: 256px; list-style: none; }
  .contacts li {
    display: flex; align-items: center; gap: 10px;
    font-size: 21px; color: var(--ink); height: 29px;
  }
  .contacts svg { width: 22px; height: 22px; flex: none; }

  .address {
    position: absolute; right: 70px; top: 260px;
    text-align: right; font-size: 21px; line-height: 1.3; color: var(--ink);
  }

  .bands {
    position: absolute; left: 0; right: 0; bottom: 0; height: 22px;
    display: flex; gap: 8px;
  }
  .bands span { flex: 1; }
  .band--blue { background: var(--blue); }
  .band--green { background: var(--green); }
  .band--yellow { background: var(--yellow); }
  .band--red { background: var(--red); }
</style>
</head>
<body>
<main class="stage">
  <section class="card card--front" aria-label="Card front">
    <div class="brand"><span class="brand__dot"></span><span class="brand__name">Nectara</span></div>
  </section>

  <section class="card card--back" aria-label="Card back">
    <div class="brand"><span class="brand__dot"></span><span class="brand__name">Nectara</span></div>

    <div class="person">
      <p class="person__name">Daniel Moreno</p>
      <p class="person__role">Manager</p>
    </div>

    <div class="divider"></div>

    <ul class="contacts">
      <li>
        <svg viewBox="0 0 24 24" aria-hidden="true"><rect width="24" height="24" rx="5" fill="var(--blue)"/><path d="M8 5.5c.6-.4 1.3-.2 1.6.4l1.1 2.3c.3.5.1 1.1-.3 1.4l-1 .7c.7 1.7 2 3 3.7 3.8l.7-1c.3-.5 1-.6 1.4-.3l2.3 1.1c.6.3.8 1 .4 1.6l-.9 1.3c-.4.6-1.2.9-1.900.7C10.600 16.3 7.700 13.4 6.500 9.1c-.2-.7.1-1.500.7-1.900z" fill="#fff"/></svg>
        <span>555-013-2468</span>
      </li>
      <li>
        <svg viewBox="0 0 24 24" aria-hidden="true"><rect width="24" height="24" rx="5" fill="var(--blue)"/><rect x="5" y="7" width="14" height="10" rx="1" fill="none" stroke="#fff" stroke-width="1.6"/><path d="M5.5 7.5 12 12.5l6.5-5M5.5 16.5l4.5-4M18.5 16.5l-4.5-4" fill="none" stroke="#fff" stroke-width="1.4"/></svg>
        <span>youremail@mailbox.com</span>
      </li>
      <li>
        <svg viewBox="0 0 24 24" aria-hidden="true"><rect width="24" height="24" rx="5" fill="var(--blue)"/><circle cx="12" cy="12" r="6.5" fill="none" stroke="#fff" stroke-width="1.6"/><ellipse cx="12" cy="12" rx="2.8" ry="6.5" fill="none" stroke="#fff" stroke-width="1.3"/><path d="M5.5 12h13" stroke="#fff" stroke-width="1.3"/></svg>
        <span>www.yourwebsite.com</span>
      </li>
    </ul>

    <p class="address">Your address, city<br>state, ZIP 0000</p>

    <div class="bands" aria-hidden="true">
      <span class="band--blue"></span>
      <span class="band--green"></span>
      <span class="band--yellow"></span>
      <span class="band--red"></span>
    </div>
  </section>
</main>
</body>
</html>
```